Business Card (double-sided) and Stationary Design for dental office

1) Business Card Design: We need a business card design for a dental specialty office.
Texts should contain:
The name of our office "Brindle Oaks Orthodontics"
Tagline: "Specialist in Orthodontic and Maxillofacial Orthopedics"
Tag line: "Creating "Tolvering" smiles for Children and Adults"
Doctor name: "Doctor Name"
Office Address:
"123 Street Name
City, State Zip code"
Office email address: office@brindleoaksortho.com
Website: www.brindleoaksortho.com

We will provide the full office address once the design is selected
Theme: beach, paradise, coastal, wave
We would like to have some creativity in design. Some acceptable ideas: front page: logo and office name. Back page: more detail information, and map to office in form of an island. Please see sample from our other location, but you DON'T HAVE TO USE OR COPY THE SAME CONCEPT.

IF POSSIBLE, PLEASE SUBMIT AT LEAST TWO CONCEPTS: ONE WITH THE BACK LOOKING SIMILAR TO WHAT IS IN THE SAMPLE, AND ONE DIFFERENT.

Color: designer to choose. We have different shade of blues and sand color in our office. Please see logo.

2) Please also design a matching set of stationary that compliment the business card and our logo.

Target Market(s)

Dental

Contact Information for Business Card

See descriptions

Font styles to use
Other font styles liked:
• Matching texts in logo

Colors
0054AA
0677BA
7BADD7
CADEEF
E8F1F8
0094D4
00A9DD
6FCCEA
C7EBF8
E9F6FB
00AB8E
00BBA5
67D7C9
C6EFE9
E9F9F6

Requirements
Must have
• Double-sided
Nice to have
• Beach coastal theme
Should not have
• Any shape or drawing of of tooth or teeth. We don’t need these. You don't necessarily have to just cut and paste the logo art and text as a whole, you have the liberty to rearrange the text.

```html
<!DOCTYPE html>
<html lang="en">
<head>
<meta charset="utf-8">
<title>Brindle Oaks Orthodontics – Business Card</title>
<link rel="stylesheet" href="https://fonts.googleapis.com/css2?family=Montserrat:wght@400;500;700&family=Arimo:wght@400&display=swap">
<style>
  :root {
    --bg: #e4e4e4;
    --card: #ffffff;
    --teal: #2f8aa6;
    --teal-deep: #237590;
    --ink: #222222;
    --rule: #c9c9c9;
    --sky: #4a8ee8;
    --sea: #a9e3e3;
    --sand: #efe6d4;
    --pin: #d6141c;
  }
  * { box-sizing: border-box; margin: 0; padding: 0; }
  html, body { width: 1200px; height: 900px; overflow: hidden; }
  body {
    background: var(--bg);
    display: flex;
    flex-direction: column;
    align-items: center;
    justify-content: center;
    gap: 44px;
    font-family: "Arimo", Arial, sans-serif;
  }
  .card {
    position: relative;
    width: 700px;
    height: 400px;
    border-radius: 30px;
    overflow: hidden;
    background: var(--card);
    box-shadow: 0 6px 16px rgba(0,0,0,0.22);
  }

  /* Front */
  .beach-scene {
    position: absolute; inset: 0;
    background:
      linear-gradient(160deg, transparent 55%, var(--sand) 56%),
      linear-gradient(180deg, var(--sky) 0%, #9cc6f2 38%, var(--sea) 50%, #cdeee6 100%);
  }
  .appointment {
    position: absolute;
    top: 34px; right: 40px;
    width: 380px; height: 190px;
    border-radius: 26px;
    background: rgba(255,255,255,0.86);
    padding: 38px 40px 0;
  }
  .appointment-title {
    font-family: "Montserrat", sans-serif;
    font-weight: 500;
    font-size: 25px;
    color: var(--teal);
    text-align: center;
  }
  .appointment-line { height: 1px; background: var(--rule); margin-top: 40px; }
  .appointment-line + .appointment-line { margin-top: 38px; }
  .location {
    position: absolute;
    left: 290px; bottom: 70px;
    display: flex; align-items: center; gap: 10px;
    font-family: "Montserrat", sans-serif;
    font-size: 21px;
    color: var(--ink);
  }

  /* Back */
  .brand {
    position: absolute;
    top: 36px; right: 42px;
    display: flex; align-items: center; gap: 12px;
  }
  .brand-mark {
    width: 34px; height: 34px; border-radius: 50%;
    background: var(--teal);
  }
  .brand-name {
    font-family: "Montserrat", sans-serif;
    font-weight: 700;
    font-size: 30px;
    color: var(--teal);
  }
  .address {
    position: absolute;
    top: 106px; right: 42px;
    text-align: right;
    font-size: 18px;
    line-height: 1.3;
    color: var(--ink);
  }
  .person { position: absolute; left: 46px; top: 168px; }
  .person-name {
    font-family: "Montserrat", sans-serif;
    font-weight: 700;
    font-size: 29px;
    line-height: 1.2;
    color: var(--teal);
  }
  .person-role { font-size: 18px; line-height: 1.3; color: var(--ink); }
  .contacts { list-style: none; margin-top: 10px; font-size: 18px; color: var(--ink); }
  .contacts li { display: flex; align-items: center; gap: 9px; line-height: 1.4; }
  .contacts svg { width: 17px; height: 17px; flex: none; }
  .divider {
    position: absolute; left: 46px; right: 42px; top: 318px;
    height: 1px; background: var(--rule);
  }
  .taglines {
    position: absolute; left: 46px; right: 42px; top: 328px;
    font-family: "Montserrat", sans-serif;
    font-weight: 500;
    font-size: 14px;
    text-transform: uppercase;
    color: var(--teal);
    line-height: 1.55;
    white-space: nowrap;
  }
  .taglines p + p { padding-left: 46px; }
</style>
</head>
<body>

  <section class="card card-front">
    <div class="beach-scene" role="img" aria-label="Photo of a tropical beach with palm trees and clear turquoise water, overlaid with a simple street map to the office"></div>
    <div class="appointment">
      <h2 class="appointment-title">Next Appointment</h2>
      <div class="appointment-line"></div>
      <div class="appointment-line"></div>
    </div>
    <div class="location">
      <svg width="20" height="26" viewBox="0 0 20 26" aria-hidden="true">
        <path d="M10 1a8 8 0 0 0-8 8c0 6 8 16 8 16s8-10 8-16a8 8 0 0 0-8-8z" fill="var(--pin)"/>
        <circle cx="10" cy="9" r="3" fill="#fff"/>
      </svg>
      <span>Brindle Oaks smiles</span>
    </div>
  </section>

  <section class="card card-back">
    <div class="brand">
      <span class="brand-mark" aria-hidden="true"></span>
      <span class="brand-name">Brindle Oaks</span>
    </div>
    <p class="address">123 Street Name<br>City, State Zip code</p>

    <div class="person">
      <h1 class="person-name">Marcus Ellery</h1>
      <p class="person-role">Managing Director</p>
      <ul class="contacts">
        <li>
          <svg viewBox="0 0 18 18" aria-hidden="true"><rect x="1" y="4" width="16" height="11" fill="var(--teal)"/><path d="M1 4l8 6 8-6" fill="none" stroke="#fff" stroke-width="1.5"/></svg>
          office@brindleoaksortho.com
        </li>
        <li>
          <svg viewBox="0 0 18 18" aria-hidden="true"><circle cx="9" cy="9" r="7.5" fill="none" stroke="var(--teal)" stroke-width="1.6"/><ellipse cx="9" cy="9" rx="3.2" ry="7.5" fill="none" stroke="var(--teal)" stroke-width="1.4"/><path d="M1.5 9h15M3 5h12M3 13h12" stroke="var(--teal)" stroke-width="1.2"/></svg>
          www.brindleoaksortho.com
        </li>
      </ul>
    </div>

    <div class="divider"></div>
    <div class="taglines">
      <p>Specialist in Orthodontic and Maxillofacial Orthopedics</p>
      <p>Creating Tolvering smiles for children and adults</p>
    </div>
  </section>

</body>
</html>
```